Velmora Consulting Business

** Please add the content information from my old business card
1. I would like to see a two sided business card with both options with the 1st Option--Tallow Spire-new WHITE BACKGROUND LOGO
2 nd Option-Tallow Spire - new BLACK- Background Logo
3rd -Option a business card with my Photo on the card
Please add the new word to the card information:
EXECUTION
AS THE OWNER'S REP
WE AIM TO ACHIEVE YOUR
INFRASTRUCTURE VISION with
OUR SPECIALIZATION & EXECUTION in:

FUNDING Planning
BUSINESS Planning
INFRASTRUCTURE Planning
PROJECT Management
Since 2012
_____________________________________________________________________
I want to get spot uv raised printing. I was liking a a nice rich white linen paper stock with black writing & NOT A COLORED CARD other than a variety of white or black cards concept

```html
<!DOCTYPE html>
<html lang="en">
<head>
<meta charset="utf-8">
<title>Velmora Consulting – Business Card</title>
<link rel="stylesheet" href="https://fonts.googleapis.com/css2?family=Arimo:wght@400;700&display=swap">
<style>
  :root {
    --backdrop: #1b1b1c;
    --card-dark: #2a2a2c;
    --card-light: #f3f3f3;
    --accent-red: #e0203a;
    --text-light: #f2f2f2;
    --ink: #1e1e1e;
    --faint-mark: #3b3b3e;
  }
  * { box-sizing: border-box; margin: 0; padding: 0; }
  html, body { width: 1200px; height: 1059px; overflow: hidden; }
  body {
    background: var(--backdrop);
    font-family: "Arimo", Arial, sans-serif;
    color: var(--text-light);
    position: relative;
  }
  .card {
    position: absolute;
    left: 255px;
    width: 690px;
    height: 390px;
    border-radius: 16px;
    background: var(--card-dark);
    overflow: hidden;
  }
  .card--front { top: 89px; }
  .card--back { top: 548px; }

  .front-swoosh { position: absolute; inset: 0; width: 690px; height: 390px; }

  .wordmark {
    position: absolute;
    left: 430px;
    top: 150px;
    width: 240px;
    text-align: center;
    color: var(--ink);
    font-weight: 700;
  }
  .wordmark__name { display: block; font-size: 50px; line-height: 1; letter-spacing: -1px; }
  .wordmark__tag { display: block; font-size: 13px; letter-spacing: 11px; margin-top: 8px; padding-left: 11px; }

  .holder { position: absolute; left: 39px; top: 125px; }
  .holder__name {
    color: var(--accent-red);
    font-weight: 700;
    font-size: 26px;
    line-height: 31px;
    width: 240px;
  }
  .holder__title { font-size: 16.5px; margin-top: 4px; }
  .rule-short { width: 22px; height: 1px; background: var(--accent-red); margin: 14px 0 12px; }
  .contact-list { list-style: none; }
  .contact-list li {
    display: flex; align-items: center; gap: 8px;
    font-size: 17px; line-height: 26.5px;
  }
  .contact-list svg { width: 13px; height: 13px; fill: var(--accent-red); flex: none; }
  .holder__offices { font-size: 17px; }

  .back-mark {
    position: absolute; top: 55px; left: 0; right: 0;
    text-align: center; color: var(--faint-mark); font-weight: 700;
  }
  .back-mark__name { display: block; font-size: 60px; line-height: 1; letter-spacing: -1px; }
  .back-mark__tag { display: block; font-size: 17px; letter-spacing: 16px; padding-left: 16px; margin-top: 6px; }

  .pitch { position: absolute; top: 164px; left: 0; right: 0; text-align: center; }
  .pitch__lead { color: var(--accent-red); font-size: 17.5px; line-height: 24px; }
  .pitch__body { font-size: 17.5px; line-height: 30px; margin-top: 5px; }

  .band-line { position: absolute; left: 0; right: 0; height: 1.5px; background: var(--accent-red); }
  .band-line--top { top: 257px; }
  .band-line--bottom { top: 354px; }

  .services { position: absolute; top: 270px; left: 0; right: 0; text-align: center; font-size: 17.5px; line-height: 32px; }
  .services .sep { color: var(--accent-red); margin: 0 5px; }

  .since {
    position: absolute; top: 343px; left: 50%; transform: translateX(-50%);
    padding: 1px 9px; border: 1.5px solid var(--accent-red); border-radius: 13px;
    background: var(--card-dark); font-size: 17.5px; line-height: 20px;
  }
</style>
</head>
<body>

<section class="card card--front" aria-label="Card front">
  <svg class="front-swoosh" viewBox="0 0 690 390" aria-hidden="true">
    <path d="M255 0 Q298 340 690 346 L690 0 Z" fill="var(--card-light)"/>
    <path d="M258 0 Q301 338 690 344 L690 0 Z" fill="var(--accent-red)"/>
    <path d="M279 0 Q326 331 690 343 L690 0 Z" fill="var(--card-light)"/>
  </svg>

  <div class="wordmark">
    <span class="wordmark__name">Velmora</span>
    <span class="wordmark__tag">CONSULTING</span>
  </div>

  <div class="holder">
    <h1 class="holder__name">Marisol Okafor-Brandt</h1>
    <p class="holder__title">CEO / Lead Project Manager</p>
    <div class="rule-short"></div>
    <ul class="contact-list">
      <li>
        <svg viewBox="0 0 16 16"><path d="M1 6c0-2 3-4 7-4s7 2 7 4v1h-4V5.5C10 5 6 5 5 5.5V7H1z M3 8h10l1 6H2z"/></svg>
        555.014.2290
      </li>
      <li>
        <svg viewBox="0 0 16 16"><path d="M1 6l7-5 7 5v9H1z M2.5 7v7h11V7L8 11z"/></svg>
        marisol@velmora.ca
      </li>
      <li>
        <svg viewBox="0 0 16 16"><path d="M8 1a7 7 0 1 0 0.01 0z M5 4l3 1 1 3-2 1-1 3-2-2 1-2-2-2z M10 10l3-1-1 3z"/></svg>
        www.velmora.ca
      </li>
    </ul>
    <div class="rule-short"></div>
    <p class="holder__offices">Harlow Bay NT • Eastmere NB</p>
  </div>
</section>

<section class="card card--back" aria-label="Card back">
  <div class="back-mark">
    <span class="back-mark__name">Velmora</span>
    <span class="back-mark__tag">CONSULTING</span>
  </div>

  <div class="pitch">
    <p class="pitch__lead">AS THE OWNER'S REP</p>
    <p class="pitch__body">WE AIM TO ACHIEVE YOUR INFRASTRUCTURE VISION<br>with OUR SPECIALIZATION &amp; EXECUTION in:</p>
  </div>

  <div class="band-line band-line--top"></div>

  <div class="services">
    <p>FUNDING Planning<span class="sep">|</span>BUSINESS Planning</p>
    <p>INFRASTRUCTURE Planning<span class="sep">|</span>PROJECT Management</p>
  </div>

  <div class="band-line band-line--bottom"></div>
  <p class="since">Since 2012</p>
</section>

</body>
</html>
```